New Business Card for Web Design/Internet Marketing Company

Looking for a great looking new business card. We are a 10 year old web design, internet marketing and website management company that works mostly with small businesses.

Our new card needs to better match the colors and style of our website, be bold, extremely usable and slightly edgy.

Target Market(s)

Small/Medium businesses that have websites

Industry/Entity Type

Internet

Requirements
Must have
• Front and back design, full color, rounded corners please

Must use the colors/style of our website (JPG provided)

INFO FOR CARDS (as readable as possible please)
Mark Lenner
President/CEO
mark@trelvanmedia.example
Phone: 520-381-7459
Toll Free: 866-381-7459
Address: 4315 W. Calloway Ave. Ste. 140, Tucson, AZ 85792

THINGS I WANT TO PROMOTE (if there is room):
1. Our Website - www.trelvanmedia.example

2. Social Media
Twitter: @trelvanmedia
Facebook: www.socialpage.example/trelvanmedia

3. Our Services
Web Design
Internet Marketing
Website Management

```html
<!DOCTYPE html>
<html lang="en">
<head>
<meta charset="utf-8">
<title>Trelvan Media – Business Card</title>
<link rel="stylesheet" href="https://fonts.googleapis.com/css2?family=Open+Sans:wght@400;600;700&display=swap">
<style>
  :root {
    --stage: #2a2a2a;
    --paper: #ffffff;
    --ink: #555a60;
    --brand-blue: #1f8fc4;
    --deep-blue: #1f4a94;
    --mid-blue: #3a78b4;
    --orange: #f07e14;
    --silver: #c4c7cb;
    --white: #ffffff;
  }
  * { margin: 0; padding: 0; box-sizing: border-box; }
  html, body { width: 1200px; height: 900px; overflow: hidden; }
  body {
    background: var(--stage);
    font-family: "Open Sans", Arial, sans-serif;
    position: relative;
  }
  .card {
    position: absolute;
    left: 253px;
    width: 669px;
    height: 381px;
    border-radius: 22px;
    overflow: hidden;
  }
  /* Front */
  .card-front { top: 66px; background: var(--paper); }
  .front-footer {
    position: absolute; left: 0; right: 0; bottom: 0; height: 58px;
    background: linear-gradient(90deg, var(--deep-blue) 0%, var(--mid-blue) 55%, var(--deep-blue) 100%);
  }
  .front-footer::before {
    content: ""; position: absolute; left: 0; right: 0; top: -10px; height: 10px;
    background: var(--orange);
  }
  .front-footer::after {
    content: ""; position: absolute; left: 0; right: 0; top: -16px; height: 4px;
    background: var(--silver);
  }
  .brand-block {
    position: absolute;
    left: 50px; top: 80px;
    width: 250px; height: 163px;
    display: flex; align-items: center; justify-content: center; gap: 10px;
  }
  .brand-dot {
    width: 22px; height: 22px; border-radius: 50%;
    background: var(--orange);
  }
  .brand-name {
    font-size: 30px; font-weight: 700; color: var(--brand-blue);
    letter-spacing: -0.5px; white-space: nowrap;
  }
  .contact {
    position: absolute; left: 398px; top: 62px;
    color: var(--ink); font-size: 15.5px; line-height: 22px;
    white-space: nowrap;
  }
  .contact-name {
    font-size: 24px; font-weight: 600; color: var(--brand-blue);
    letter-spacing: 0.5px; line-height: 28px;
  }
  .contact-title { margin-bottom: 38px; }
  .contact-address { margin-bottom: 14px; }
  .contact-label { color: var(--brand-blue); }
  .contact-line { line-height: 24px; }

  /* Back */
  .card-back {
    top: 478px;
    background: radial-gradient(ellipse at 15% 10%, #5a9ccc 0%, #3a6fae 40%, var(--deep-blue) 80%);
    color: var(--white);
  }
  .back-glow {
    position: absolute; left: 260px; top: 40px; width: 480px; height: 440px;
    border-radius: 50%;
    background: radial-gradient(circle, rgba(255,255,255,0.12) 0%, rgba(255,255,255,0) 65%);
  }
  .services { position: absolute; left: 34px; top: 34px; }
  .services-title {
    color: var(--orange); font-size: 22px; font-weight: 600; margin-bottom: 4px;
  }
  .service-list { list-style: none; font-size: 18px; line-height: 25px; }
  .service-list li { display: flex; align-items: center; gap: 6px; }
  .bullet {
    width: 14px; height: 8px; border: 1.5px solid var(--orange);
    border-bottom: none; border-radius: 14px 14px 0 0;
  }
  .social { position: absolute; left: 34px; top: 172px; font-size: 18px; line-height: 29px; }
  .social li { list-style: none; display: flex; align-items: center; gap: 9px; white-space: nowrap; }
  .social-square { width: 17px; height: 17px; background: var(--orange); border-radius: 2px; }
  .site-link { color: var(--orange); font-size: 18px; }
  .back-brand {
    position: absolute; right: 30px; bottom: 22px;
    font-size: 46px; font-weight: 700; color: var(--white);
    letter-spacing: -0.5px; white-space: nowrap;
  }
</style>
</head>
<body>

<section class="card card-front" aria-label="Business card front">
  <div class="front-footer"></div>

  <div class="brand-block">
    <span class="brand-dot"></span>
    <span class="brand-name">Trelvan Media</span>
  </div>

  <div class="contact">
    <p class="contact-name">Mark Lenner</p>
    <p class="contact-title">President/CEO</p>
    <p class="contact-address">4315 W. Calloway Ave.<br>Ste. 140, Tucson, AZ 85792</p>
    <p class="contact-line"><span class="contact-label">Phone.</span> 520-381-7459</p>
    <p class="contact-line"><span class="contact-label">Toll Free.</span> 866-381-7459</p>
    <p class="contact-line"><span class="contact-label">Email.</span> mark@trelvanmedia.example</p>
  </div>
</section>

<section class="card card-back" aria-label="Business card back">
  <div class="back-glow"></div>
  <div class="services">
    <h2 class="services-title">Our Service</h2>
    <ul class="service-list">
      <li><span class="bullet"></span>Web Design</li>
      <li><span class="bullet"></span>Internet Marketing</li>
      <li><span class="bullet"></span>Website Management</li>
    </ul>
  </div>
  <ul class="social">
    <li><span class="social-square"></span>@trelvanmedia</li>
    <li><span class="social-square"></span>www.socialpage.example/trelvanmedia</li>
    <li class="site-link">www.trelvanmedia.example</li>
  </ul>
  <p class="back-brand">Trelvan Media</p>
</section>

</body>
</html>
```